Web Design Project

We have a website in beta that needs updating and are looking for a freash new look for the Home page including Logo.
Our company is called " Kip Dorra " we specialize in classified advertising using video. Our consumers will be businesses selling a product or service. Please visit www.kipdorra.com
Our aim past this point is to engage a developer to write the code based on the best design. Our target market is the U.S and I have included some of the landing pages to give you a better idea of what we are trying to acheive

http://www.kipdorra.com/
http://www.kipdorra.com/cars_home.php
http://www.kipdorra.com/boats.php
http://www.kipdorra.com/electronic.php
http://www.kipdorra.com/realestate.php
http://www.kipdorra.com/roommates.php
Updates

Target Market(s)

20-35 yr old people who are connected to the internet via mobile phone and use social media on a daily/weekly basis

Industry/Entity Type

Advertising

Requirements
Must have
• We would like to use lots of images to convey it is a video driven website business
Nice to have
• Logo to incorporate same theme of website ( ie ) you are here to watch videos of thinhs to buy & sell
Should not have
• This is to be a freash new site with large type and bold fonts

```html
<!DOCTYPE html>
<html lang="en">
<head>
<meta charset="utf-8">
<title>Kip Dorra – Video Classifieds</title>
<link href="https://fonts.googleapis.com/css2?family=Open+Sans:wght@400;600;700&display=swap" rel="stylesheet">
<style>
:root{
  --orange:#e2561a;
  --orange-dark:#b8320f;
  --red-title:#a8321a;
  --ink:#2b2b2b;
  --muted:#555;
  --band:#efefef;
  --footer:#ececec;
  --footer-bar:#dcdcdc;
  --black:#151515;
}
*{box-sizing:border-box;margin:0;padding:0}
html,body{width:686px;height:1200px;overflow:hidden;background:#fff;font-family:"Open Sans",Arial,sans-serif;color:var(--ink)}
.page{position:relative;width:686px;height:1200px}
.abs{position:absolute}

/* header */
.brand{left:48px;top:24px}
.brand-name{display:flex;align-items:center;gap:6px;font-size:26px;font-weight:700;color:#3a3a3a;line-height:1}
.brand-dot{width:22px;height:22px;border-radius:50%;background:var(--orange)}
.brand-tag{margin-top:6px;font-size:9.5px;font-weight:700;color:#444;line-height:1.35}
.brand-tag b{font-size:13px;display:block}
.sign-in{left:517px;top:18px;width:44px;height:18px;background:var(--black);color:#fff;font-size:8px;line-height:18px;text-align:center;border-radius:2px}
.lang{left:572px;top:17px;width:63px;height:20px;border:1px solid #ccc;font-size:7px;line-height:18px;padding-left:5px;color:#333}
.lang .flag{position:absolute;left:24px;top:6px;width:15px;height:8px;background:#2d3f8f;border:1px solid #c33}
.lang .caret{position:absolute;right:5px;top:7px;width:0;height:0;border:4px solid transparent;border-top:4px solid #333}
.nav{left:302px;top:70px;display:flex;gap:0;font-size:8.6px;color:#333}
.nav a{display:block;height:20px;line-height:20px;padding:0 7.5px;text-decoration:none;color:#333}
.nav a.active{background:var(--orange);color:#fff;position:relative}
.nav a.active::after{content:"";position:absolute;right:4px;bottom:-5px;border:3px solid transparent;border-top:3px solid var(--orange);border-left:3px solid var(--orange)}

/* hero */
.hero{left:0;top:116px;width:686px;height:284px;background:linear-gradient(160deg,#d8d5cf 0%,#9ea3a6 35%,#6f6a63 65%,#b9b2a8 100%)}
.hero-caption{left:49px;top:161px;width:506px;height:56px;background:rgba(40,40,40,.72);color:#fff;font-size:16px;font-weight:600;letter-spacing:.6px;line-height:56px;padding-left:16px}
.dots{left:312px;top:411px;display:flex;gap:2px}
.dots span{width:13px;height:13px;border-radius:50%;background:#e6e6e6;border:1px solid #d6d6d6}
.dots span.on{background:#2a2a2a;border-color:#2a2a2a}

.welcome{left:0;top:438px;width:686px;text-align:center}
.welcome h1{font-size:12px;font-weight:700;color:var(--red-title);letter-spacing:.5px}
.welcome p{width:584px;margin:8px auto 0;font-size:7.6px;line-height:12.4px;color:#333}

/* steps */
.steps{left:0;top:533px;width:686px;height:162px;background:var(--band)}
.step{position:absolute;top:12px;width:110px;text-align:center}
.step .ring{width:108px;height:108px;border-radius:50%;background:#e5e5e5;margin:0 auto;display:flex;align-items:center;justify-content:center;box-shadow:inset 0 0 6px #d0d0d0}
.step .disc{width:92px;height:92px;border-radius:50%;background:radial-gradient(circle at 50% 30%,#e8601e,#b8320f 85%);display:flex;align-items:center;justify-content:center}
.step .btn{display:inline-block;margin-top:10px;background:var(--black);color:#fff;font-size:8.4px;font-weight:700;letter-spacing:.4px;padding:0 11px;height:24px;line-height:24px;border-radius:2px;box-shadow:0 2px 2px rgba(0,0,0,.25)}

/* featured */
.featured{left:128px;top:718px;width:428px;height:270px;border:1px solid #e2e2e2}
.featured-bar{left:133px;top:724px;width:419px;height:38px;background:linear-gradient(#2a2a2a,#050505);border-radius:2px}
.featured-bar h2{position:absolute;left:13px;top:0;line-height:38px;color:#fff;font-size:10px;font-weight:600;letter-spacing:.3px}
.tabs{position:absolute;right:5px;top:11px;display:flex;gap:7px}
.tabs span{background:#eaeaea;color:#222;font-size:7.6px;height:16px;line-height:16px;padding:0 5px;border-radius:1px}
.thumb{width:132px;height:102px}

/* footer */
.footer{left:0;top:1036px;width:686px;height:122px;background:var(--footer)}
.fcol{position:absolute;top:10px;font-size:7.3px;color:#444}
.fcol h3{display:flex;align-items:center;gap:5px;font-size:8.8px;font-weight:700;color:#333;height:20px;margin-bottom:6px}
.fcol li{list-style:none;height:16.4px}
.social li{display:flex;align-items:center;gap:6px;height:27px}
.social .sq{width:18px;height:18px;border-radius:4px}
.copy{left:0;top:1158px;width:686px;height:42px;background:var(--footer-bar);font-size:7.3px;color:#444;line-height:42px;padding-left:49px}
</style>
</head>
<body>
<div class="page">

  <header>
    <div class="abs brand">
      <div class="brand-name"><span>Kip Dorra</span><span class="brand-dot"></span></div>
      <div class="brand-tag">Buy and sell through the<b>#1 Video Classifieds</b></div>
    </div>
    <div class="abs sign-in">SIGN IN</div>
    <div class="abs lang">ENG<span class="flag"></span><span class="caret"></span></div>
    <nav class="abs nav">
      <a class="active" href="#">Cars</a><a href="#">Boats</a><a href="#">Electronics</a><a href="#">Real Estate</a><a href="#">Roommates</a><a href="#">Other Categories</a>
    </nav>
  </header>

  <section class="abs hero" role="img" aria-label="Photo looking down from a rooftop ledge at a city street, sneakers in the foreground"></section>
  <div class="abs hero-caption">WE SPECIALIZE IN CLASSIFIED ADVERTISING USING VIDEOS</div>
  <div class="abs dots"><span class="on"></span><span></span><span></span><span></span></div>

  <section class="abs welcome">
    <h1>WELCOME TO KIP DORRA</h1>
    <p>Lorem ipsum dolor sit amet, consectetuer adipiscing elit, sed diam nonummy nibh euismod tincidunt ut laoreet dolore magna aliquam erat volutpat. Ut wisi enim ad minim veniam, quis nostrud exerci tation ullamcorper suscipit lobortis nisl ut aliquip ex ea commodo consequat. Duis autem vel eum iriure dolor in hendrerit in vulputate velit esse molestie consequat, vel illum dolore eu feugiat nulla facilisis at vero eros et accumsan et iusto odio dignissim qui blandit praesent luptatum zzril delenit augue duis dolore te feugait nulla facilisi.</p>
  </section>

  <section class="abs steps">
    <div class="step" style="left:121px">
      <div class="ring"><div class="disc">
        <svg width="40" height="40" viewBox="0 0 40 40" fill="none" stroke="#fff" stroke-width="4"><path d="M22 6H6v28h28V18"/><path d="M18 24l2-7 13-13 5 5-13 13z" fill="#fff" stroke-width="1"/></svg>
      </div></div>
      <div class="btn">CREATE IT</div>
    </div>
    <div class="step" style="left:293px">
      <div class="ring"><div class="disc">
        <svg width="46" height="46" viewBox="0 0 46 46" fill="none" stroke="#fff" stroke-width="3.5"><circle cx="23" cy="23" r="19"/><circle cx="23" cy="23" r="11"/><path d="M23 16l-10 11h6v13h8V27h6z" fill="#fff" stroke="#c23a12" stroke-width="1.5"/></svg>
      </div></div>
      <div class="btn">UPLOAD IT</div>
    </div>
    <div class="step" style="left:459px">
      <div class="ring"><div class="disc">
        <svg width="54" height="44" viewBox="0 0 54 44" fill="none" stroke="#fff" stroke-width="3" stroke-linejoin="round"><path d="M27 4l23 12-23 12L4 16z" fill="#fff"/><path d="M4 23l23 12 23-12"/><path d="M4 30l23 12 23-12"/></svg>
      </div></div>
      <div class="btn">SELL IT</div>
    </div>
  </section>

  <section>
    <div class="abs featured"></div>
    <div class="abs featured-bar">
      <h2>Browse Featured Kip Dorra</h2>
      <div class="tabs"><span>Most Viewed</span><span>Most Recent</span><span>Most Interesting</span></div>
    </div>
    <div class="abs thumb" style="left:133px;top:771px;background:linear-gradient(#f4f4f4,#2a2a2a 60%,#555)" role="img" aria-label="Black SUV"></div>
    <div class="abs thumb" style="left:277px;top:771px;background:linear-gradient(#7fa6d8,#dfe9f5 45%,#2f5f8e 75%)" role="img" aria-label="White motor yacht on the water"></div>
    <div class="abs thumb" style="left:418px;top:771px;background:linear-gradient(#b6bcc2,#e5e2dc 55%,#8a7a66)" role="img" aria-label="Private jet on a runway at sunset"></div>
    <div class="abs thumb" style="left:133px;top:881px;background:linear-gradient(#7a6a58,#8ea34a 70%,#5d6b2e)" role="img" aria-label="Roommate relaxing on a green sofa in a bedroom"></div>
    <div class="abs thumb" style="left:277px;top:881px;background:linear-gradient(#b9d2ea,#9a9c7c 45%,#8a5a48)" role="img" aria-label="Two-storey suburban house with a garage"></div>
    <div class="abs thumb" style="left:418px;top:881px;background:linear-gradient(#fafafa,#9a9a9a 55%,#1e1e1e)" role="img" aria-label="Home theater speakers and television"></div>
  </section>

  <footer>
    <div class="abs footer">
      <div class="fcol" style="left:48px">
        <h3><svg width="20" height="16" viewBox="0 0 20 16"><path d="M2 6l8-4 8 4v8l-8 2-8-2z" fill="#f2c14a"/><path d="M2 6l8 3 8-3" stroke="#c8912a" fill="none"/></svg>Buy / Browse</h3>
        <ul><li>Roommates</li><li>Cars</li><li>Boats</li><li>Electronics</li><li>Others</li></ul>
      </div>
      <div class="fcol" style="left:160px">
        <h3><svg width="18" height="16" viewBox="0 0 18 16"><rect x="1" y="3" width="16" height="10" rx="1" fill="#a9c49a"/><circle cx="9" cy="8" r="3" fill="#7c9a6c"/></svg>Sell</h3>
        <ul><li>About us</li><li>meet the team</li><li>experience</li><li>testimonials</li></ul>
      </div>
      <div class="fcol" style="left:274px">
        <h3><svg width="18" height="18" viewBox="0 0 18 18"><circle cx="9" cy="9" r="8" fill="#f0a020"/><rect x="8" y="7" width="2" height="7" fill="#fff"/><circle cx="9" cy="4.5" r="1.2" fill="#fff"/></svg>Our Work</h3>
        <ul><li>Faculty</li><li>Events</li><li>Products</li><li>Articles</li><li>Media Center</li></ul>
      </div>
      <div class="fcol" style="left:402px">
        <h3><svg width="12" height="18" viewBox="0 0 12 18"><rect x="1" y="1" width="10" height="16" rx="2" fill="#333"/><rect x="3" y="4" width="6" height="8" fill="#8fb8d8"/></svg>Contact</h3>
        <ul><li>Contact Us</li><li>Feedback Form</li><li>Referral Program</li><li>Business Register</li><li>Subscription</li></ul>
      </div>
      <div class="fcol" style="left:542px">
        <h3><svg width="16" height="18" viewBox="0 0 16 18"><circle cx="8" cy="5" r="4" fill="#e6b98f"/><path d="M1 18c0-6 14-6 14 0z" fill="#4a7fc1"/></svg>Connect Us</h3>
        <ul class="social">
          <li><span class="sq" style="background:#3b5a9a"></span>Friendline</li>
          <li><span class="sq" style="background:#3aa7e0"></span>Chirper</li>
          <li><span class="sq" style="background:#ef7a1a"></span>Rss Feed</li>
        </ul>
      </div>
    </div>
    <div class="abs copy">© 2013 Kip Dorra. All Rights Reserved.</div>
  </footer>

</div>
</body>
</html>
```